Vorn upkeep KT Solar Venture

Solar power system install
Services and maintenance
wiring, Rewinding and Renovation
Switch Board Upgrade
Power and lighting point
t doesn’t matter how much you spend on quality parts, your solar system will let you down if your design and installation are sub-par. Have your solar system tailored and installed by our Master Electrician and Bright Grid Guild Accredited team.

Target Market(s)

sales and installed

Industry/Entity Type

Solar install and retailer

Contact Information for Business Card

Name , Email, Phone Number ,Business address,

Font styles to use
Serif

Colors
0054AA
0677BA
7BADD7
CADEEF
E8F1F8

Requirements
Must have
• clear and bright
Nice to have
• new design
Should not have
• unclear pictures

```html
<!DOCTYPE html>
<html lang="en">
<head>
<meta charset="utf-8">
<title>Vorn upkeep · KT Solar Venture – Business Card</title>
<link rel="stylesheet" href="https://fonts.googleapis.com/css2?family=Roboto:wght@400;500;700&family=Roboto+Condensed:wght@700&display=swap">
<style>
  :root {
    --bg: #2b2b2b;
    --blue-deep: #0054AA;
    --blue: #0677BA;
    --blue-soft: #7BADD7;
    --blue-pale: #CADEEF;
    --blue-mist: #E8F1F8;
    --green: #2fa23a;
    --green-light: #6db33f;
    --ink: #1d1d1d;
    --white: #ffffff;
    --silver: #e6e6e6;
  }
  * { box-sizing: border-box; margin: 0; padding: 0; }
  html, body { width: 1200px; height: 1138px; overflow: hidden; }
  body {
    background: var(--bg);
    font-family: "Roboto", Arial, sans-serif;
    position: relative;
  }
  .card {
    position: absolute;
    border-radius: 16px;
    overflow: hidden;
  }

  /* Front */
  .card-front {
    left: 274px; top: 186px; width: 622px; height: 376px;
    background: linear-gradient(100deg, var(--blue) 0%, #1792a0 45%, #4cab5a 80%, var(--green-light) 100%);
  }
  .front-brand {
    position: absolute; left: 102px; top: 50px;
    display: flex; align-items: center; gap: 24px;
  }
  .brand-dot {
    width: 110px; height: 110px; border-radius: 50%;
    background: radial-gradient(circle at 40% 40%, #f6c52a, #e88a1c 60%, var(--green) 100%);
  }
  .brand-name {
    font-family: "Roboto Condensed", "Roboto", sans-serif;
    font-weight: 700; font-size: 32px; line-height: 1.15;
    color: var(--white); letter-spacing: 0.5px; text-transform: uppercase;
  }
  .services-band {
    position: absolute; left: 0; top: 239px; width: 100%; height: 73px;
    background: linear-gradient(180deg, #f4f4f4, var(--silver));
    display: flex; flex-direction: column; justify-content: center; align-items: center;
    gap: 4px;
    font-size: 16px; color: var(--ink);
  }
  .front-web {
    position: absolute; left: 0; top: 331px; width: 100%;
    display: flex; justify-content: center; align-items: center; gap: 24px;
    color: var(--white); font-size: 15px;
  }
  .front-web .rule { width: 80px; height: 2px; background: rgba(255,255,255,0.7); }

  /* Back */
  .card-back {
    left: 276px; top: 608px; width: 618px; height: 374px;
    background: linear-gradient(180deg, #f8f8f8, #e9e9e9);
  }
  .back-wave { position: absolute; left: 0; top: 0; }
  .holder {
    position: absolute; right: 30px; top: 30px; text-align: right; color: var(--white);
  }
  .holder-name { font-size: 25px; font-weight: 500; }
  .holder-role { font-size: 16px; margin-top: 6px; }
  .back-brand {
    position: absolute; left: 30px; top: 120px; width: 290px;
    display: flex; flex-direction: column; align-items: center; gap: 22px;
  }
  .back-brand .brand-dot { width: 130px; height: 130px; }
  .back-brand .brand-name { color: var(--blue-deep); font-size: 33px; text-align: center; }
  .contact {
    position: absolute; right: 30px; top: 212px;
    text-align: right; font-size: 16px; color: var(--ink); line-height: 24px;
  }
  .contact-lines { list-style: none; margin-top: 12px; }
  .contact-lines li { display: flex; justify-content: flex-end; align-items: center; gap: 14px; }
  .contact-lines svg { width: 16px; height: 16px; fill: var(--green); }
</style>
</head>
<body>

<section class="card card-front">
  <div class="front-brand">
    <div class="brand-dot" role="img" aria-label="Company symbol area"></div>
    <div class="brand-name">Vorn Upkeep<br>KT Solar Venture</div>
  </div>
  <div class="services-band">
    <p>Solar Power System Install &nbsp;|&nbsp; Wiring, Rewinding &amp; Renovation</p>
    <p>Services &amp; Maintenance &nbsp;|&nbsp; Switch Board Upgrade &nbsp;|&nbsp; Power &amp; Lighting Point</p>
  </div>
  <div class="front-web">
    <span class="rule"></span>
    <span>www.ktsolarventure.com</span>
    <span class="rule"></span>
  </div>
</section>

<section class="card card-back">
  <svg class="back-wave" width="618" height="150" viewBox="0 0 618 150">
    <path d="M0,0 H618 V118 C500,128 420,70 300,40 C200,18 90,20 0,40 Z" fill="var(--blue)"/>
    <path d="M0,50 C90,26 200,26 300,50 C420,82 500,136 618,122" fill="none" stroke="var(--green)" stroke-width="7"/>
    <path d="M40,56 C140,30 240,40 310,60" fill="none" stroke="var(--green-light)" stroke-width="3"/>
  </svg>
  <div class="holder">
    <div class="holder-name">Dana Ellis Reed</div>
    <div class="holder-role">Managing Director</div>
  </div>
  <div class="back-brand">
    <div class="brand-dot" role="img" aria-label="Company symbol area"></div>
    <div class="brand-name">Vorn Upkeep<br>KT Solar Venture</div>
  </div>
  <div class="contact">
    <address style="font-style: normal;">87 Harbor Row, Linden Vale,<br>Brookfield, US 400218</address>
    <ul class="contact-lines">
      <li>555-014-2290
        <svg viewBox="0 0 16 16" aria-hidden="true"><path d="M3 2h3l1.5 3.5-2 1.3a9 9 0 0 0 3.7 3.7l1.3-2L14 10v3a1 1 0 0 1-1 1A11 11 0 0 1 2 3a1 1 0 0 1 1-1z"/></svg>
      </li>
      <li>dana@ktsolarventure.com
        <svg viewBox="0 0 16 16" aria-hidden="true"><path d="M1 3h14v10H1z M2 4.2v.4L8 9l6-4.4v-.4z" fill-rule="evenodd"/></svg>
      </li>
      <li>www.ktsolarventure.com
        <svg viewBox="0 0 16 16" aria-hidden="true"><circle cx="8" cy="8" r="6.5" fill="none" stroke="var(--green)" stroke-width="1.5"/><path d="M1.5 8h13M8 1.5c-3 3.5-3 9.5 0 13M8 1.5c3 3.5 3 9.5 0 13" fill="none" stroke="var(--green)" stroke-width="1.2"/></svg>
      </li>
    </ul>
  </div>
</section>

</body>
</html>
```